Stationery Design + Business Cards

Stationary (letterhead as A4 210x297mm and Letter 8.5"x11", preferably both master page + 2nd pages)

Also need business cards, standard size 50x88mm, can be vertical or horizontal.

You can use a front/back design for the business cards, or front only.

Looking at the uploaded file (devank, you already have that), I want it to use the first logo on the list (4 colors).

Alternative, try the grayscale version (second file).

I need the following information on the business card (in no particular order, let me know what you come up with): 

Firstname Lastlame 
Title 

Mobile +1 555-204-7391 

VelaMorn, Inc. 
24851 Birchwood Ridge Passage 
Alderholm, WA 46099 
Tel. +1 555-368-4172 
Fax +1 555-619-0834 

Web: www.velamorn.example 
Twitter: twitter/VelaMorn or @VelaMorn 
Facebook: facebook.com/VelaMorn 

For letterhead, just the company name, address + phone number & fax number 

If you think the phone/fax or something else should not be on the business cards, or something could be missing, let me know.

```html
<!DOCTYPE html>
<html lang="en">
<head>
<meta charset="utf-8">
<title>VelaMorn Letterhead 8.5x11</title>
<link rel="stylesheet" href="https://fonts.googleapis.com/css2?family=Source+Sans+3:wght@400;600;700&display=swap">
<style>
  :root {
    --board: #000000;
    --paper: #ffffff;
    --brand-blue: #1d4f9e;
    --rule: #8a98b8;
    --label: #ffffff;
  }
  * { margin: 0; padding: 0; box-sizing: border-box; }
  html, body {
    width: 900px;
    height: 1200px;
    overflow: hidden;
    background: var(--board);
    font-family: "Source Sans 3", "Myriad Pro", Arial, sans-serif;
  }
  .board {
    position: relative;
    width: 900px;
    height: 1200px;
  }
  .board-title {
    position: absolute;
    top: 35px;
    left: 0;
    width: 860px;
    text-align: center;
    color: var(--label);
    font-weight: 700;
    font-size: 18px;
    line-height: 22px;
    letter-spacing: 0.2px;
  }
  .letterhead {
    position: absolute;
    left: 42px;
    top: 68px;
    width: 822px;
    height: 1064px;
    background: var(--paper);
    overflow: hidden;
  }
  .brand {
    position: absolute;
    left: 74px;
    top: 60px;
    display: flex;
    align-items: center;
    gap: 14px;
  }
  .brand-dot {
    width: 40px;
    height: 40px;
    border-radius: 50%;
    background: var(--brand-blue);
  }
  .brand-name {
    color: var(--brand-blue);
    font-weight: 400;
    font-size: 46px;
    line-height: 1;
    letter-spacing: -0.3px;
  }
  .contact {
    position: absolute;
    left: 463px;
    top: 78px;
    padding-left: 9px;
    border-left: 1px solid var(--rule);
    color: var(--brand-blue);
    font-style: normal;
    font-weight: 600;
    font-size: 11.8px;
    line-height: 16px;
    white-space: nowrap;
  }
</style>
</head>
<body>
  <main class="board">
    <h1 class="board-title">Letter Head 8.5x11 Inch</h1>
    <section class="letterhead">
      <div class="brand">
        <span class="brand-dot"></span>
        <span class="brand-name">VelaMorn</span>
      </div>
      <address class="contact">
        VelaMorn, Inc., 24851 Birchwood Ridge Passage,<br>
        Alderholm, WA 46099, Tel. +1 555-368-4172, Fax +1 555-619-0834
      </address>
    </section>
  </main>
</body>
</html>
```